Artwork for New Single, ”Keep Still”

Unique design describing Silence.
Use the pictures provided for ideas.
Looking for something out the box, different.
Make this stand out. Modern times or futuristic.
Imagination welcomed.
BRINDLE ENTERTAINMENT INC.
Artist name is Brindle
Song Title: Keep Still

Target Market(s)

Millennials, Trap music listeners, Hardcore rap fans.

Colors

Designer to choose colors to be used in the design.

Requirements
Nice to have
• Bold, serious designs. Make a statement. Masculine, professional in nature.

```html
<!DOCTYPE html>
<html lang="en">
<head>
<meta charset="utf-8">
<title>Keep Still — Brindle — cover type studies</title>
<link rel="stylesheet" href="https://fonts.googleapis.com/css2?family=Alfa+Slab+One&family=Amarante&family=Caveat+Brush&family=Cutive+Mono&family=Special+Elite&family=Mr+Dafoe&family=Rubik+Dirt&family=Courier+Prime:wght@700&family=Metal+Mania&display=swap">
<style>
  :root {
    --navy-deep: #0b1422;
    --navy: #132540;
    --navy-light: #1f4670;
    --print-grey: #b4bcc6;
    --print-shadow: #6f7986;
    --stamp-red: #e50b0b;
    --stamp-red-dark: #c40909;
    --white: #ffffff;
    --silver: #c9d3dc;
    --ice: #8fd3ff;
    --ice-deep: #2a8fe0;
    --divider: #c8c8c8;
  }
  html, body {
    margin: 0;
    padding: 0;
    width: 1200px;
    height: 2400px;
    overflow: hidden;
    background: var(--divider);
  }
  .sheet {
    position: relative;
    width: 1200px;
    height: 2400px;
    display: grid;
    grid-template-columns: 599px 599px;
    grid-template-rows: repeat(4, 599px);
    gap: 2px;
  }
  .cover {
    position: relative;
    overflow: hidden;
  }
  .cover__art {
    position: absolute;
    inset: 0;
    background:
      radial-gradient(ellipse 200px 250px at 310px 160px, rgba(180,188,198,0.55), rgba(180,188,198,0) 72%),
      radial-gradient(ellipse 230px 150px at 310px 420px, rgba(180,188,198,0.75), rgba(180,188,198,0) 75%),
      radial-gradient(ellipse 320px 120px at 520px 470px, rgba(111,121,134,0.35), rgba(111,121,134,0) 75%),
      radial-gradient(ellipse 260px 100px at 200px 590px, rgba(60,110,170,0.35), rgba(60,110,170,0) 75%),
      linear-gradient(180deg, var(--navy-deep) 0%, var(--navy) 55%, var(--navy-light) 100%);
  }
  .stamp {
    position: absolute;
    left: 22px;
    top: 200px;
    width: 560px;
    height: 190px;
    transform: rotate(3deg);
    transform-origin: left top;
  }
  .stamp__rule {
    position: absolute;
    background: var(--stamp-red-dark);
  }
  .stamp__rule--top { left: 14px; top: 4px; width: 546px; height: 11px; }
  .stamp__rule--inner { left: 4px; top: 24px; width: 540px; height: 2px; opacity: .75; }
  .stamp__rule--bottom { left: 0; top: 146px; width: 548px; height: 5px; }
  .stamp__rule--base { left: 50px; top: 166px; width: 500px; height: 4px; opacity: .85; }
  .stamp__rule--side { left: 548px; top: 42px; width: 8px; height: 136px; }
  .stamp__title {
    position: absolute;
    left: 14px;
    top: 30px;
    margin: 0;
    font-family: "Alfa Slab One", serif;
    font-size: 80px;
    line-height: 1;
    letter-spacing: -2px;
    color: var(--stamp-red);
    white-space: nowrap;
    transform: scaleY(1.3);
    transform-origin: left top;
  }
  .artist {
    position: absolute;
    left: 0;
    right: 0;
    margin: 0;
    text-align: center;
    color: var(--white);
    white-space: nowrap;
    font-weight: 400;
  }
  .artist--engraved { top: 478px; font-family: "Amarante", serif; font-size: 78px; color: var(--silver); letter-spacing: -1px; }
  .artist--brush { top: 440px; font-family: "Caveat Brush", cursive; font-size: 118px; }
  .artist--typewriter { top: 496px; font-family: "Cutive Mono", monospace; font-size: 68px; letter-spacing: 26px; padding-left: 26px; }
  .artist--worn { top: 496px; font-family: "Special Elite", monospace; font-size: 64px; letter-spacing: 24px; padding-left: 24px; }
  .artist--signature { top: 460px; font-family: "Mr Dafoe", cursive; font-size: 108px; }
  .artist--distressed { top: 494px; font-family: "Rubik Dirt", sans-serif; font-size: 66px; }
  .artist--mono { top: 510px; font-family: "Courier Prime", monospace; font-weight: 700; font-size: 56px; letter-spacing: 30px; padding-left: 30px; }
  .artist--frost {
    top: 486px;
    font-family: "Metal Mania", cursive;
    font-size: 88px;
    background: linear-gradient(180deg, var(--ice) 0%, var(--white) 45%, var(--ice-deep) 100%);
    -webkit-background-clip: text;
    background-clip: text;
    color: transparent;
  }
</style>
</head>
<body>
<main class="sheet">

  <section class="cover">
    <div class="cover__art" role="img" aria-label="Photo of a pale handprint over dark blue grunge background with zippers"></div>
    <div class="stamp"><span class="stamp__rule stamp__rule--top"></span><span class="stamp__rule stamp__rule--inner"></span><h1 class="stamp__title">KEEP STILL</h1><span class="stamp__rule stamp__rule--bottom"></span><span class="stamp__rule stamp__rule--base"></span><span class="stamp__rule stamp__rule--side"></span></div>
    <p class="artist artist--engraved">Brindle</p>
  </section>

  <section class="cover">
    <div class="cover__art" role="img" aria-label="Photo of a pale handprint over dark blue grunge background with zippers"></div>
    <div class="stamp"><span class="stamp__rule stamp__rule--top"></span><span class="stamp__rule stamp__rule--inner"></span><h1 class="stamp__title">KEEP STILL</h1><span class="stamp__rule stamp__rule--bottom"></span><span class="stamp__rule stamp__rule--base"></span><span class="stamp__rule stamp__rule--side"></span></div>
    <p class="artist artist--brush">Brindle</p>
  </section>

  <section class="cover">
    <div class="cover__art" role="img" aria-label="Photo of a pale handprint over dark blue grunge background with zippers"></div>
    <div class="stamp"><span class="stamp__rule stamp__rule--top"></span><span class="stamp__rule stamp__rule--inner"></span><h1 class="stamp__title">KEEP STILL</h1><span class="stamp__rule stamp__rule--bottom"></span><span class="stamp__rule stamp__rule--base"></span><span class="stamp__rule stamp__rule--side"></span></div>
    <p class="artist artist--typewriter">BRINDLE</p>
  </section>

  <section class="cover">
    <div class="cover__art" role="img" aria-label="Photo of a pale handprint over dark blue grunge background with zippers"></div>
    <div class="stamp"><span class="stamp__rule stamp__rule--top"></span><span class="stamp__rule stamp__rule--inner"></span><h1 class="stamp__title">KEEP STILL</h1><span class="stamp__rule stamp__rule--bottom"></span><span class="stamp__rule stamp__rule--base"></span><span class="stamp__rule stamp__rule--side"></span></div>
    <p class="artist artist--worn">BRINDLE</p>
  </section>

  <section class="cover">
    <div class="cover__art" role="img" aria-label="Photo of a pale handprint over dark blue grunge background with zippers"></div>
    <div class="stamp"><span class="stamp__rule stamp__rule--top"></span><span class="stamp__rule stamp__rule--inner"></span><h1 class="stamp__title">KEEP STILL</h1><span class="stamp__rule stamp__rule--bottom"></span><span class="stamp__rule stamp__rule--base"></span><span class="stamp__rule stamp__rule--side"></span></div>
    <p class="artist artist--signature">Brindle</p>
  </section>

  <section class="cover">
    <div class="cover__art" role="img" aria-label="Photo of a pale handprint over dark blue grunge background with zippers"></div>
    <div class="stamp"><span class="stamp__rule stamp__rule--top"></span><span class="stamp__rule stamp__rule--inner"></span><h1 class="stamp__title">KEEP STILL</h1><span class="stamp__rule stamp__rule--bottom"></span><span class="stamp__rule stamp__rule--base"></span><span class="stamp__rule stamp__rule--side"></span></div>
    <p class="artist artist--distressed">Brindle</p>
  </section>

  <section class="cover">
    <div class="cover__art" role="img" aria-label="Photo of a pale handprint over dark blue grunge background with zippers"></div>
    <div class="stamp"><span class="stamp__rule stamp__rule--top"></span><span class="stamp__rule stamp__rule--inner"></span><h1 class="stamp__title">KEEP STILL</h1><span class="stamp__rule stamp__rule--bottom"></span><span class="stamp__rule stamp__rule--base"></span><span class="stamp__rule stamp__rule--side"></span></div>
    <p class="artist artist--mono">BRINDLE</p>
  </section>

  <section class="cover">
    <div class="cover__art" role="img" aria-label="Photo of a pale handprint over dark blue grunge background with zippers"></div>
    <div class="stamp"><span class="stamp__rule stamp__rule--top"></span><span class="stamp__rule stamp__rule--inner"></span><h1 class="stamp__title">KEEP STILL</h1><span class="stamp__rule stamp__rule--bottom"></span><span class="stamp__rule stamp__rule--base"></span><span class="stamp__rule stamp__rule--side"></span></div>
    <p class="artist artist--frost">BRINDLE</p>
  </section>

</main>
</body>
</html>
```